Business Card Design needed for start up company Halvora

In need of a new business card designed for a start up company based in Sydney, Halvora is a new start up innovative Company, our mission it to make property accessible for everyday Australian and to become the leading Real Estate platform in Australia. We want it to be fresh and clean.

Industry/Entity Type

Financial

Contact Information for Business Card

Section for Name
Section for Title

HALVORA - The Strength of Pooling
Mobile:
Direct:

Font styles to use
Sans Serif

Colors
33a6d7
0692cd
0255a3
ffffff

Requirements
Must have
• Logo, all business card details

```html
<!DOCTYPE html>
<html lang="en">
<head>
<meta charset="utf-8">
<title>Halvora Business Card</title>
<link href="https://fonts.googleapis.com/css2?family=Lato:wght@400;700;900&display=swap" rel="stylesheet">
<style>
  :root {
    --sky: #33a6d7;
    --ocean: #0692cd;
    --navy: #1f4a80;
    --deep: #0255a3;
    --white: #ffffff;
    --mist: #edf2f9;
    --backdrop: #e4e7ec;
  }
  * { box-sizing: border-box; margin: 0; padding: 0; }
  html, body { width: 1200px; height: 880px; overflow: hidden; }
  body {
    background: var(--backdrop);
    font-family: "Lato", sans-serif;
    position: relative;
  }
  .card {
    position: absolute;
    width: 620px;
    height: 354px;
    border-radius: 18px;
    overflow: hidden;
    box-shadow: 0 10px 28px rgba(0,0,0,.18);
  }
  /* Back side */
  .card-back {
    left: 60px; top: 60px;
    background: var(--navy);
    display: flex; align-items: center; justify-content: center; gap: 18px;
  }
  .brand-dot {
    width: 96px; height: 96px; border-radius: 50%;
    background: var(--ocean);
    flex: none;
  }
  .brand-name {
    font-weight: 900;
    color: var(--white);
    font-size: 78px;
    letter-spacing: -1px;
    line-height: 1;
  }
  /* Front side */
  .card-front {
    left: 520px; top: 466px;
    background: var(--white);
  }
  .faint-circle {
    position: absolute;
    left: 10px; top: 20px;
    width: 270px; height: 270px; border-radius: 50%;
    background: var(--mist);
  }
  .front-logo {
    position: absolute;
    left: 250px; top: 34px;
    display: flex; align-items: center; gap: 12px;
  }
  .front-logo .brand-dot { width: 66px; height: 66px; }
  .front-logo .brand-name { color: var(--navy); font-size: 48px; }
  .tagline {
    position: absolute;
    left: 328px; top: 92px;
    font-size: 13px; color: var(--navy); letter-spacing: .6px;
  }
  .person {
    position: absolute;
    left: 44px; top: 122px;
  }
  .person-name {
    font-weight: 900; color: var(--navy); font-size: 22px; letter-spacing: .2px;
  }
  .person-title { color: var(--ocean); font-size: 16px; margin-top: 2px; }
  .contacts {
    position: absolute;
    left: 150px; top: 200px;
    list-style: none;
  }
  .contacts li {
    display: flex; align-items: center; gap: 8px;
    font-size: 16px; color: var(--navy); margin-bottom: 5px;
  }
  .contact-icon {
    width: 18px; height: 18px; border-radius: 50%;
    background: var(--ocean);
    display: flex; align-items: center; justify-content: center; flex: none;
  }
  .address {
    position: absolute;
    right: 36px; top: 146px;
    text-align: right;
    font-size: 14px; color: var(--navy); line-height: 1.3;
  }
  .wave { position: absolute; left: 0; top: 0; width: 620px; height: 354px; }
</style>
</head>
<body>
  <section class="card card-back" aria-label="Card back">
    <span class="brand-dot"></span>
    <span class="brand-name">HALVORA</span>
  </section>

  <section class="card card-front" aria-label="Card front">
    <div class="faint-circle"></div>
    <svg class="wave" viewBox="0 0 620 354" aria-hidden="true">
      <path d="M0,322 C170,320 345,302 445,268 C515,244 568,220 620,204" fill="none" stroke="var(--ocean)" stroke-width="5"/>
      <path d="M0,336 C170,333 350,314 452,280 C520,257 572,234 620,220 L620,354 L0,354 Z" fill="var(--navy)"/>
    </svg>

    <div class="front-logo">
      <span class="brand-dot"></span>
      <span class="brand-name">HALVORA</span>
    </div>
    <p class="tagline">The Strength of Pooling</p>

    <div class="person">
      <p class="person-name">MARA QUINLAN</p>
      <p class="person-title">Owner</p>
    </div>

    <ul class="contacts">
      <li>
        <span class="contact-icon"><svg width="8" height="11" viewBox="0 0 8 11"><rect x="0.5" y="0.5" width="7" height="10" rx="1.5" fill="none" stroke="#fff"/><circle cx="4" cy="8.5" r=".8" fill="#fff"/></svg></span>
        0412 555 018
      </li>
      <li>
        <span class="contact-icon"><svg width="11" height="9" viewBox="0 0 11 9"><path d="M1,3 C3,0 8,0 10,3 L8,4 L7,2.5 L4,2.5 L3,4 Z" fill="#fff"/><rect x="2.5" y="5" width="6" height="3.5" rx="1" fill="#fff"/></svg></span>
        0412 555 018
      </li>
      <li>
        <span class="contact-icon"><svg width="11" height="8" viewBox="0 0 11 8"><rect x=".5" y=".5" width="10" height="7" fill="#fff"/><path d="M.5,.5 L5.5,4.5 L10.5,.5" fill="none" stroke="var(--ocean)"/></svg></span>
        mara@halvoramail.com
      </li>
    </ul>

    <p class="address">PO BOX 482 Harbour Lane<br>Sydney NSW, Australia</p>
  </section>
</body>
</html>
```